Candle Rental Business seeks new website design

We need a new website design for a Candle hire business. The business rents out pillar candles for events such as weddings and corporate events. Our main target market is weddings. The business name is Hire a Lantern. The business name does not have a logo design.

We would like a website that is light in colours and creates a warm atmosphere. The design needs to be elegant and upmarket. There are different size candles that we hire out, ranging from 10cm diameter to 20cm diameter, flat, tall etc. All our candles are white in colour. Its just the size that differs.

We would also like to include a section for hiring out decor such as glassvases, candlebras, overlays and chairs sachets, chair covers. However, this is not the businesses main focus but an additional offering to customers.

Target Market(s)

Wedding venues and brides. Corporate events. School dances.

Industry/Entity Type

Hospitality

Logo Text

Hire a Lantern

Number of Pages Required

1 page

Font styles to use
Sans Serif
Script

Requirements
Must have
• Pictures of pillar candles. Plain white candles. The website must centre around candles.
Nice to have
• Different examples of candle centrepieces
Should not have
• Pictures must not be of brides. Pictures of surrounding is perferable.

```html
<!DOCTYPE html>
<html lang="en">
<head>
<meta charset="utf-8">
<title>Hire a Lantern</title>
<link href="https://fonts.googleapis.com/css2?family=Roboto+Slab:wght@300;400;500&family=Kaushan+Script&display=swap" rel="stylesheet">
<style>
:root{
  --gold:#e2aa2c;
  --rust:#c9602b;
  --green:#7fa33a;
  --cream:#f5f1e8;
  --ink:#4a4a4a;
  --muted:#7a7a7a;
  --white:#ffffff;
}
*{margin:0;padding:0;box-sizing:border-box}
html,body{width:768px;height:1200px;overflow:hidden}
body{position:relative;background:var(--white);font-family:"Roboto Slab",Georgia,serif;color:var(--ink)}
.abs{position:absolute}

/* hero */
.hero{left:0;top:0;width:768px;height:349px;background:radial-gradient(ellipse at 50% 60%,#c89a5a 0%,#8a6236 45%,#3e3a30 100%)}
.hero-glow{left:0;top:0;width:768px;height:160px;background:linear-gradient(180deg,rgba(80,150,160,.35),rgba(0,0,0,0))}
.nav{left:84px;top:0;width:600px;height:42px;background:var(--gold)}
.nav a{position:absolute;top:14px;font-size:10.5px;color:var(--white);text-decoration:none}
.brand{left:296px;top:-30px;width:160px;height:110px;border-radius:0 0 80px 80px;background:var(--white);display:flex;align-items:center;justify-content:center;padding-top:34px}
.brand-name{font-size:16px;font-weight:500;color:var(--rust)}
.hero-title{left:0;top:158px;width:768px;text-align:center;font-family:"Kaushan Script",cursive;font-size:31px;color:var(--white)}
.thumb{top:280px;width:85px;height:45px;border:2px solid var(--white)}
.thumb.active:before{content:"";position:absolute;left:38px;top:-8px;border:5px solid transparent;border-bottom:4px solid var(--white)}

/* about */
.section-title{font-size:15.5px;font-weight:400;color:var(--ink)}
.section-title span{color:var(--rust)}
.dot{display:inline-block;width:9px;height:9px;border-radius:50%;background:var(--green);vertical-align:middle;margin:0 8px}
.about-title{left:0;top:373px;width:768px;text-align:center}
.about-text{left:84px;top:408px;width:600px;text-align:center;font-size:8.6px;line-height:15.6px;color:var(--muted);font-weight:300}

/* services */
.band{left:0;top:484px;width:768px;height:338px;background:var(--cream)}
.card{background:var(--white)}
.card h3{font-size:15px;font-weight:400;color:var(--rust)}
.card p{font-size:7.4px;line-height:13.2px;color:var(--muted);font-weight:300}
.btn{display:inline-block;background:var(--green);color:var(--white);font-size:7.4px;padding:4px 10px}
.photo{display:block}

/* gallery */
.gallery-title{left:84px;top:844px}
.gal{width:127px;height:71px}
.quote{left:524px;top:857px;width:160px;height:176px;background:var(--gold)}
.avatar{left:578px;top:844px;width:52px;height:52px;border-radius:50%;background:linear-gradient(135deg,#d9d2c4,#8a7a66);border:2px solid var(--white)}
.quote p{position:absolute;left:12px;top:50px;width:136px;text-align:center;font-size:7.2px;line-height:13.3px;color:var(--white);font-weight:300}
.quote .who{position:absolute;left:0;top:133px;width:160px;text-align:center;font-size:9px;color:var(--rust)}
.pager{position:absolute;top:160px;height:2px;background:rgba(255,255,255,.5)}

/* footer */
.footer{left:0;top:1057px;width:768px;height:143px;background:var(--rust)}
.f-head{font-size:11.5px;color:var(--gold)}
.f-text{font-size:8.6px;line-height:13.5px;color:var(--white)}
.social{top:1104px;width:19px;height:19px}
.f-rule{left:84px;top:1142px;width:600px;height:1px;background:rgba(255,255,255,.25)}
.f-links{left:0;top:1156px;width:768px;text-align:center;font-size:8.4px;color:var(--white)}
.f-links span{margin:0 5px}
.copy{left:0;top:1173px;width:768px;text-align:center;font-size:8.2px;color:var(--white)}
</style>
</head>
<body>

<header>
  <div class="abs hero" role="img" aria-label="Banquet table lit by white pillar candles among pale roses"></div>
  <div class="abs hero-glow"></div>
  <nav class="abs nav">
    <a style="left:24px">Home</a>
    <a style="left:82px">About Us</a>
    <a style="left:154px">Services</a>
    <a style="left:394px">Products</a>
    <a style="left:465px">Gallery</a>
    <a style="left:528px">Contact Us</a>
  </nav>
  <div class="abs brand"><span class="brand-name">Hire a Lantern</span></div>
  <h1 class="abs hero-title" style="font-weight:400">Meaningful gift at a friendly price point</h1>
  <div class="abs thumb active" style="left:242px;background:linear-gradient(135deg,#e9d7b6,#a97c45)" role="img" aria-label="Candlelit reception table"></div>
  <div class="abs thumb" style="left:342px;background:linear-gradient(135deg,#2b2118,#c98d3c)" role="img" aria-label="Tall pillar candles glowing"></div>
  <div class="abs thumb" style="left:442px;background:linear-gradient(135deg,#d7c2a8,#f3ede4)" role="img" aria-label="Hands lighting a pillar candle"></div>
</header>

<section>
  <h2 class="abs section-title about-title"><i class="dot"></i>About <span>Hire a Lantern</span><i class="dot"></i></h2>
  <p class="abs about-text">We are a family owned and operated company and began making decorative candles for all occasions. All of our candles are individually hand made in our candle studio, situated in Brackenfield, outside Larkmoor. Our wax is local and of a very high quality, and dripless! Our wax is also made with a high melting point, which means it will not melt or bend in hot temperatures.</p>
</section>

<section class="abs band"></section>

<article class="abs card" style="left:84px;top:509px;width:225px;height:295px">
  <div class="abs photo" style="left:12px;top:10px;width:201px;height:120px;background:linear-gradient(135deg,#cfc6b4,#f4f1ea 55%,#8fb6c4)" role="img" aria-label="White pillar candles on a glass centrepiece"></div>
  <h3 class="abs" style="left:12px;top:144px">Hire Candles</h3>
  <p class="abs" style="left:12px;top:168px;width:201px">Do you love using candles for your events but tired of sorting old used candles or buying expensive candles. Believe it or not you can now rent candles. All our candles come in different sizes and heights. You can add the ambience of candlelight to your event of wedding ceremony without the worry over dripping wax or open candle flames.</p>
  <span class="abs btn" style="left:12px;top:266px">Read More</span>
</article>

<article class="abs card" style="left:321px;top:509px;width:363px;height:141px">
  <h3 class="abs" style="left:12px;top:8px">Personalised Candles</h3>
  <p class="abs" style="left:12px;top:35px;width:208px">Hire a Lantern provides the opportunity to give a thoughtful, meaningful gift at a friendly price point. This unique gift conveys the time and care you put into creating it. The recipient will enjoy the beautiful presentation and be reminded of the sentiment...</p>
  <span class="abs btn" style="left:12px;top:112px">Read More</span>
  <div class="abs photo" style="left:229px;top:10px;width:124px;height:124px;background:linear-gradient(135deg,#e9e9eb,#c9c6c9)" role="img" aria-label="Two personalised candles in glass jars"></div>
</article>

<article class="abs card" style="left:321px;top:662px;width:363px;height:142px">
  <h3 class="abs" style="left:12px;top:8px">Décor Hire</h3>
  <p class="abs" style="left:12px;top:35px;width:212px">We hire a selection of overlays, chair sachets and chair covers as well as glassware and candelabras to compliment your decor.</p>
  <span class="abs btn" style="left:12px;top:86px">Read More</span>
  <div class="abs photo" style="left:232px;top:12px;width:120px;height:119px;background:linear-gradient(160deg,#6e1e1a,#4f6a2c 70%,#e8e4d8)" role="img" aria-label="Glass candle centrepiece with white roses"></div>
</article>

<section>
  <h2 class="abs section-title gallery-title">Our <span>Photo Gallery</span><i class="dot"></i></h2>
  <div class="abs gal" style="left:84px;top:878px;background:linear-gradient(135deg,#e6ded2,#b27a48)" role="img" aria-label="Candelabras with white tapers"></div>
  <div class="abs gal" style="left:223px;top:878px;background:linear-gradient(135deg,#1f5f86,#8bc7df)" role="img" aria-label="Blue-lit table with candle centrepiece"></div>
  <div class="abs gal" style="left:362px;top:878px;background:linear-gradient(135deg,#2a2015,#c79447)" role="img" aria-label="Single pillar candle on a stand"></div>
  <div class="abs gal" style="left:84px;top:962px;background:linear-gradient(135deg,#2a1a10,#d8a15a)" role="img" aria-label="Row of white candles glowing"></div>
  <div class="abs gal" style="left:223px;top:962px;background:linear-gradient(135deg,#1f150e,#c08a4a)" role="img" aria-label="Candles among flower arrangements"></div>
  <div class="abs gal" style="left:362px;top:962px;background:linear-gradient(135deg,#b8a690,#f2ede4)" role="img" aria-label="Candle lighting at a ceremony table"></div>

  <aside class="abs quote">
    <p>"There are many variations of passages of Lorem Ipsum available, but the majority have suffered alteration in some form, by injected humour, or randomised words which don't look even slightly believable."</p>
    <div class="who">Marla Ostin</div>
    <span class="pager" style="left:50px;width:18px;background:var(--white)"></span>
    <span class="pager" style="left:71px;width:18px"></span>
    <span class="pager" style="left:92px;width:18px"></span>
  </aside>
  <div class="abs avatar" role="img" aria-label="Customer portrait"></div>
</section>

<footer class="abs footer"></footer>
<div class="abs f-head" style="left:85px;top:1079px">Location</div>
<div class="abs f-text" style="left:85px;top:1097px">Simply dummy text printing<br>typesetting AT 12356</div>
<div class="abs" style="left:0;top:1084px;width:768px;text-align:center;font-size:11.5px;color:var(--gold)">+100 555 0142</div>
<div class="abs" style="left:0;top:1101px;width:768px;text-align:center;font-size:11.5px;color:var(--white);font-weight:500">hello@hirealantern.example</div>
<div class="abs f-head" style="left:584px;top:1079px;width:100px;text-align:right">Follow us</div>
<span class="abs social" style="left:586px;background:#3b5998" aria-label="Social link"></span>
<span class="abs social" style="left:612px;background:#1da1f2" aria-label="Social link"></span>
<span class="abs social" style="left:638px;background:#0a66c2" aria-label="Social link"></span>
<span class="abs social" style="left:665px;background:#d8402f" aria-label="Social link"></span>
<div class="abs f-rule"></div>
<div class="abs f-links">Home<span>|</span>About Us<span>|</span>Services<span>|</span>Products<span>|</span>Gallery<span>|</span>Contact Us</div>
<div class="abs copy">© 2016 Hire a Lantern, All Rights Reserved</div>

</body>
</html>
```